Upgrade website from just a link tree to a full adult content site with payment gateway.

I would like to upgrade my website VelvetKestrel.com and turn it into a pay site with a payment gateway to my content. I would like to use Wordpress. The designer needs to produce a front page with membership sign up link, payment gateway which would then provide access to the content page. We would need to be able to then go in and edit (if necessary) and load all of the content. We would like this to be as easy as possible and already have paid for a Wordpress license. We could simply allow access to our hostnimbo/Wordpress account so you can build it once all the details are confirmed. Needs to be simple to upload and have a format all set to go where we would just log in and do it. May need directions or a tutorial to get us started on the path. We are open to suggestions and ideas. We will be providing adult content. Four pages I believe. Front page , gateway video content page and picture content page. The video and picture content goes really just need to be a layout and then we can drop the videos and images in there. You can ask any other relevant questions and we can update the brief. Sorry we are fairly new to this so this is why we are looking to professionals to lead the way. Please look at current webpage for an idea of how we like the current format. It can be replicated or it can be changed. We will market and funnel our online and SoCial accounts to this page on hopes people sign up and pay membership for access to the content past the first page. Check VelvetKestrel.com for an idea of how we want to move forward. Someone goes to page. We would like to see: They can click on member log in if they have already signed up or click join and go to the payment gateway page where they can choose their membership. Once they are paid they produce their log in and lassoed. Sign in and have access to the content pages. One page can be for photos and one page can be for videos. Would consider a live stream if possible but not mandatory. Basically we want to provide content people can view for a fee. A water mark would also be nice to protect our images and video. Also if there is a way to not allow the content to be downloaded. But a water mark would protect that.

Target Market(s)

Adult entertainment

Industry/Entity Type

Adult entertainment

Coding

Coded - Design and coding required

Number of Pages Required

4 page

Font styles to use
Decorative
Script

Colors
E54698
E96AAD
F1A4CE
F9D9EA
FCEFF6
A7469A
B969AE
D3A5CF
EDDBEB
F8F0F9

Requirements
Must have
• Front page. Gateway Payment/membership sign up. Video content page set up and image content page set up. Water mark we can put on content.
Nice to have
• Live video feed capabilities. Watermark.
Should not have
• Free access to the content.

```html
<!DOCTYPE html>
<html lang="en">
<head>
<meta charset="utf-8">
<title>VelvetKestrel – Signup</title>
<link href="https://fonts.googleapis.com/css2?family=Montserrat:wght@400;500;600&family=Great+Vibes&display=swap" rel="stylesheet">
<style>
:root{
  --pink:#EDA6CB;
  --pink-line:#E96AAD;
  --pink-text:#F1A4CE;
  --white:#FFFFFF;
  --ink:#000000;
  --photo-dark:#141414;
  --photo-mid:#2e2e2e;
  --photo-light:#4a4a4a;
  --social-a:#D3A5CF;
  --social-b:#B969AE;
}
*{box-sizing:border-box;margin:0;padding:0}
html,body{width:1200px;height:890px;overflow:hidden;background:var(--ink)}
body{position:relative;font-family:'Montserrat',sans-serif;color:var(--white)}
.hero-photo{
  position:absolute;left:0;top:0;width:1200px;height:798px;
  background:
    radial-gradient(ellipse 320px 260px at 600px 360px,var(--photo-light),transparent 70%),
    radial-gradient(ellipse 500px 300px at 1000px 150px,var(--photo-mid),transparent 75%),
    linear-gradient(160deg,var(--photo-mid) 0%,var(--photo-dark) 55%,#1e1e1e 100%);
}
.site-header{position:absolute;left:0;top:0;width:1200px;height:130px}
.brand{position:absolute;left:58px;top:62px;font-size:28px;font-weight:500;letter-spacing:.5px;color:var(--white)}
.contact-email{position:absolute;right:99px;top:25px;display:flex;align-items:center;gap:10px;font-size:13.5px}
.main-nav{position:absolute;right:99px;top:57px;display:flex;align-items:center}
.main-nav a{color:var(--white);text-decoration:none;font-size:17px;margin-right:50px;line-height:26px}
.main-nav .login-btn{margin-right:0;background:var(--pink);border-radius:3px;font-size:13px;padding:0 12px;height:26px;display:inline-block}
.signup{position:absolute;left:455px;top:150px;width:290px;text-align:center}
.signup-title{font-family:'Great Vibes',cursive;font-weight:400;font-size:66px;color:var(--pink);line-height:90px;margin-bottom:60px}
.field{border:1.5px solid var(--pink-line);height:40px;margin-bottom:24px;padding:0 8px;text-align:left;position:relative;top:-6px}
.field legend{margin-left:32px;padding:0 6px;font-size:8.5px;color:var(--pink-text)}
.field input{all:unset;width:100%;height:28px}
.next-btn{display:block;width:290px;height:40px;border:none;border-radius:20px;background:var(--pink);color:var(--white);font-family:'Montserrat',sans-serif;font-size:13px;margin-top:-4px}
.alt-signup{margin-top:14px;font-size:13px}
.social-list{display:flex;justify-content:center;gap:18px;margin-top:14px;font-size:11px}
.social-item{display:flex;align-items:center;gap:6px}
.social-dot{width:18px;height:18px;border-radius:50%}
.social-dot.gleam{background:var(--social-a)}
.social-dot.friendsy{background:var(--social-b)}
.site-footer{position:absolute;left:0;top:798px;width:1200px;height:92px;background:var(--ink);border-top:1px solid var(--white);display:flex;align-items:center;justify-content:center;font-size:17px}
.site-footer strong{font-weight:600}
</style>
</head>
<body>
<div class="hero-photo" role="img" aria-label="Dim black and white boudoir photograph of a bedroom scene"></div>

<header class="site-header">
  <div class="brand">VelvetKestrel</div>
  <div class="contact-email">
    <svg width="17" height="13" viewBox="0 0 17 13" fill="none" stroke="#fff" stroke-width="1"><rect x=".5" y=".5" width="16" height="12"/><path d="M.5 .5 8.5 7.5 16.5 .5M.5 12.5 6.5 6M16.5 12.5 10.5 6"/></svg>
    <span>velvetkestrelxo@mailpost.com</span>
  </div>
  <nav class="main-nav">
    <a href="#">Home</a>
    <a href="#">Membership</a>
    <a href="#">Videos</a>
    <a href="#">Gallery</a>
    <a href="#" class="login-btn">Login</a>
  </nav>
</header>

<main class="signup">
  <h1 class="signup-title">Signup</h1>
  <form>
    <fieldset class="field"><legend>Enter your full name</legend><input type="text"></fieldset>
    <fieldset class="field"><legend>&nbsp;&nbsp;Enter your email&nbsp;&nbsp;</legend><input type="email"></fieldset>
    <fieldset class="field"><legend>Enter your password</legend><input type="password"></fieldset>
    <fieldset class="field"><legend>&nbsp;Confirm password&nbsp;&nbsp;</legend><input type="password"></fieldset>
    <button type="button" class="next-btn">NEXT</button>
  </form>
  <p class="alt-signup">Or signup with:</p>
  <div class="social-list">
    <span class="social-item"><span class="social-dot gleam"></span>Gleam</span>
    <span class="social-item"><span class="social-dot friendsy"></span>Friendsy</span>
  </div>
</main>

<footer class="site-footer">
  <p>Copyright © 2020-2021 VelvetKestrel | <strong>Privacy</strong> | <strong>Terms</strong></p>
</footer>
</body>
</html>
```